Australian Trucking Company Requires Professional Looking Stationary

We require a professional looking stationary design that incorporates our newly designed logo.

Our business, called "Brell Haulage Contracting", provides contracting work, transport and logistics to business in Western Australia particularly with links to the mining sector.

We are a small business looking to expand and our new logo and our new stationary will help develop our brand image in our market place.

Target Market(s)

Businesses and Corporation with links to the Mining Sector

Industry/Entity Type

Small Business

Requirements
Must have
• The letterhead must have the following details:
The new logo

Text saying: "Brell Holdings Pty Ltd (ACN 582 316 907) ATF The Brell Discretionary Trust T/AS"
"ABN 71 834 209 553"
Address "P.O Box 817 Wattlegrove WA, 6958"
Phone: 08 9352 7140
Email: brellhaul@mailbox-example.com.au

The text on the letterhead should be editable as the details are likely to change in the near future. Provision should be made for a website address all though one isn't available at the moment.

The styling, layout and font text is entirely up to the designer.

```html
<!DOCTYPE html>
<html lang="en">
<head>
<meta charset="utf-8">
<title>Brell Haulage Contracting – Business Cards</title>
<link rel="stylesheet" href="https://fonts.googleapis.com/css2?family=Open+Sans:wght@400;600;800&display=swap">
<style>
  :root {
    --bg: #ecebe8;
    --card: #ffffff;
    --brand-red: #d8202a;
    --brand-red-dark: #b5141d;
    --swoosh-grey: #9a9a9a;
    --text-dark: #333333;
    --text-grey: #555555;
    --text-light: #ffffff;
    --shadow: rgba(0, 0, 0, 0.18);
  }
  * { box-sizing: border-box; margin: 0; padding: 0; }
  html, body {
    width: 1200px;
    height: 650px;
    overflow: hidden;
    background: var(--bg);
    font-family: "Open Sans", Arial, sans-serif;
  }
  .stage {
    width: 1200px;
    height: 650px;
    display: flex;
    align-items: center;
    justify-content: center;
    gap: 40px;
  }
  .card {
    position: relative;
    width: 540px;
    height: 310px;
    background: var(--card);
    border-radius: 22px;
    overflow: hidden;
    box-shadow: 0 10px 24px var(--shadow);
  }
  .card-wave {
    position: absolute;
    inset: 0;
    width: 100%;
    height: 100%;
  }

  /* Front */
  .brand {
    position: absolute;
    top: 26px;
    left: 28px;
    display: flex;
    align-items: center;
    gap: 18px;
  }
  .brand-mark {
    width: 60px;
    height: 60px;
    background: var(--text-grey);
  }
  .brand-name {
    color: var(--brand-red);
    font-weight: 800;
    font-size: 27px;
    line-height: 1.02;
    text-transform: uppercase;
    letter-spacing: 0.5px;
  }
  .postal {
    position: absolute;
    top: 112px;
    left: 28px;
    display: flex;
    align-items: center;
    gap: 6px;
    font-size: 13px;
    color: var(--text-dark);
  }
  .postal svg { width: 12px; height: 12px; fill: var(--text-dark); }
  .entity {
    position: absolute;
    top: 138px;
    left: 28px;
    font-size: 11px;
    line-height: 1.45;
    color: var(--text-grey);
  }
  .contact {
    position: absolute;
    right: 26px;
    top: 160px;
    list-style: none;
    text-align: right;
    color: var(--text-light);
    font-size: 12px;
    line-height: 1.75;
  }
  .contact li { display: flex; justify-content: flex-end; align-items: center; gap: 5px; }
  .contact svg { width: 11px; height: 11px; fill: var(--text-light); }
  .holder {
    position: absolute;
    left: 28px;
    bottom: 26px;
    color: var(--text-light);
    font-size: 19px;
  }
  .holder-name { font-weight: 600; }

  /* Back */
  .back {
    display: flex;
    flex-direction: column;
    align-items: center;
    justify-content: center;
    gap: 44px;
  }
  .back-brand {
    display: flex;
    align-items: center;
    gap: 18px;
  }
  .back-brand .brand-mark { width: 78px; height: 78px; }
  .back-brand .brand-name { font-size: 34px; color: var(--text-grey); }
  .back-web {
    font-size: 22px;
    color: var(--text-dark);
    letter-spacing: 1px;
  }
</style>
</head>
<body>
  <main class="stage">
    <section class="card front" aria-label="Business card front">
      <svg class="card-wave" viewBox="0 0 540 310" preserveAspectRatio="none" aria-hidden="true">
        <defs>
          <linearGradient id="redBand" x1="0" y1="0" x2="1" y2="0">
            <stop offset="0" stop-color="var(--brand-red-dark)"/>
            <stop offset="1" stop-color="var(--brand-red)"/>
          </linearGradient>
          <linearGradient id="greySwoosh" x1="0" y1="0" x2="1" y2="0">
            <stop offset="0" stop-color="#cfcfcf"/>
            <stop offset="0.5" stop-color="var(--swoosh-grey)"/>
            <stop offset="1" stop-color="#d6d6d6"/>
          </linearGradient>
        </defs>
        <path d="M0,186 C150,241 330,156 540,48" fill="none" stroke="url(#greySwoosh)" stroke-width="7"/>
        <path d="M0,205 C150,255 330,170 540,60 L540,310 L0,310 Z" fill="url(#redBand)"/>
      </svg>

      <div class="brand">
        <span class="brand-mark" aria-hidden="true"></span>
        <p class="brand-name">Brell<br>Haulage<br>Contracting</p>
      </div>

      <p class="postal">
        <svg viewBox="0 0 12 12" aria-hidden="true"><path d="M6 1 L11.5 6 H10 V11 H7.2 V8 H4.8 V11 H2 V6 H0.5 Z"/></svg>
        P.O Box 817 Wattlegrove WA, 6958
      </p>
      <p class="entity">Brell Holdings Pty Ltd (ACN 582 316 907)<br>ATF The Brell Discretionary Trust T/AS</p>

      <ul class="contact">
        <li><svg viewBox="0 0 12 12" aria-hidden="true"><path d="M3 1 L5 3.6 L3.8 5 C4.5 6.5 5.5 7.5 7 8.2 L8.4 7 L11 9 L9.8 11 C5 10.6 1.4 7 1 2.2 Z"/></svg>08 9352 7140</li>
        <li><svg viewBox="0 0 12 12" aria-hidden="true"><path d="M1 2.5 H11 V9.5 H1 Z M1.6 3 L6 6.6 L10.4 3 Z" fill-rule="evenodd"/></svg>brellhaul@mailbox-example.com.au</li>
        <li><svg viewBox="0 0 12 12" aria-hidden="true"><circle cx="6" cy="6" r="5"/></svg>www.brellhaulage.com.au</li>
        <li>ABN 71 834 209 553</li>
      </ul>

      <p class="holder"><span class="holder-name">Your Name,</span> Title</p>
    </section>

    <section class="card back" aria-label="Business card back">
      <div class="back-brand">
        <span class="brand-mark" aria-hidden="true"></span>
        <p class="brand-name">Brell<br>Haulage<br>Contracting</p>
      </div>
      <p class="back-web">www.brellhaulage.com.au</p>
    </section>
  </main>
</body>
</html>
```